Fern Lattice Table & Chair Rentals

We need a business card for a table and chair rental company. We rent tables and chairs for weddings, funerals, business events and parties. We want something that looks clean and elegant while not being too busy. We would like colors in the green and blue hues and avoiding anything orange. We want to make sure the font is large enough to be seen easily.

Target Market(s)

Wedding & Event Rentals

Industry/Entity Type

Events

Contact Information for Business Card

Fern Lattice, sales@fernlatticerentals.com, fernlatticerentals.com, 360-555-0182

Requirements
Must have
• Easy to read font
Should not have
• Orange anywhere in the design

```html
<!DOCTYPE html>
<html lang="en">
<head>
<meta charset="utf-8">
<title>Fern Lattice Table &amp; Chair Rentals – Business Card</title>
<link href="https://fonts.googleapis.com/css2?family=Open+Sans:wght@400;600&display=swap" rel="stylesheet">
<style>
  :root {
    --page-bg: #e6e9e8;
    --card-white: #fbfcfb;
    --ink: #2f3a38;
    --ink-soft: #44504d;
    --accent: #2f8f7a;
    --accent-light: #7cc3b2;
    --back-light: #5fb6a4;
    --back-mid: #2e8a86;
    --back-deep: #1f5f7a;
    --photo-green: #7c9b62;
    --photo-pale: #e8ece4;
    --photo-soft: #c9d9c6;
    --white: #ffffff;
  }
  * { box-sizing: border-box; margin: 0; padding: 0; }
  html, body {
    width: 1200px; height: 885px; overflow: hidden;
    background: var(--page-bg);
    font-family: "Open Sans", Arial, sans-serif;
  }
  .canvas {
    position: relative; width: 1200px; height: 885px;
    display: flex; flex-direction: column; align-items: center; justify-content: center;
    gap: 40px;
  }
  .card {
    position: relative; width: 680px; height: 388px; overflow: hidden;
    box-shadow: 0 6px 18px rgba(0,0,0,0.18);
  }

  /* Front */
  .card-front { background: var(--card-white); }
  .front-art { position: absolute; inset: 0; }
  .front-info { position: absolute; left: 300px; top: 50px; right: 30px; color: var(--ink); }
  .brand-name { font-weight: 600; font-size: 44px; line-height: 1.1; color: var(--ink); white-space: nowrap; }
  .brand-tagline { font-size: 24px; line-height: 1.3; margin-top: 2px; color: var(--ink-soft); white-space: nowrap; }
  .contact-name { font-weight: 600; font-size: 34px; line-height: 1.2; margin-top: 26px; white-space: nowrap; }
  .contact-list { list-style: none; margin-top: 14px; font-size: 19px; line-height: 1.4; }
  .contact-rule { height: 2px; background: var(--accent); margin: 10px 0 8px; width: 330px; }
  .contact-web { font-size: 19px; line-height: 1.4; white-space: nowrap; }

  /* Back */
  .card-back {
    background: linear-gradient(120deg, var(--back-light) 0%, var(--back-mid) 55%, var(--back-deep) 100%);
    color: var(--white);
  }
  .back-pattern { position: absolute; inset: 0; }
  .back-info { position: absolute; left: 250px; top: 80px; }
  .back-info .brand-name { color: var(--white); font-size: 52px; }
  .back-info .brand-tagline { color: var(--white); font-size: 27px; }
  .back-web { position: absolute; left: 60px; bottom: 40px; font-size: 24px; line-height: 1.3; white-space: nowrap; }
  .back-rule { position: absolute; left: 420px; bottom: 55px; width: 260px; height: 2px; background: var(--white); }
</style>
</head>
<body>
<main class="canvas">

  <section class="card card-front">
    <svg class="front-art" width="680" height="388" viewBox="0 0 680 388">
      <defs>
        <linearGradient id="photoTone" x1="0" y1="0" x2="1" y2="1">
          <stop offset="0" stop-color="#e8ece4"/>
          <stop offset="0.45" stop-color="#a9c196"/>
          <stop offset="0.7" stop-color="#c9d9c6"/>
          <stop offset="1" stop-color="#7c9b62"/>
        </linearGradient>
      </defs>
      <path role="img" aria-label="Photo of a floral table centrepiece with white chairs"
            d="M0 0 H170 C235 90 300 230 250 388 H0 Z" fill="url(#photoTone)"/>
      <path d="M170 0 C235 90 300 230 250 388" fill="none" stroke="var(--accent)" stroke-width="5"/>
      <path d="M185 0 C250 95 312 235 266 388" fill="none" stroke="var(--accent-light)" stroke-width="2"/>
    </svg>
    <div class="front-info">
      <div class="brand-name">Fern Lattice</div>
      <div class="brand-tagline">Table and Chair Rentals</div>
      <div class="contact-name">Fern Lattice</div>
      <ul class="contact-list">
        <li>360-555-0182</li>
        <li>sales@fernlatticerentals.com</li>
      </ul>
      <div class="contact-rule"></div>
      <div class="contact-web">www.fernlatticerentals.com</div>
    </div>
  </section>

  <section class="card card-back">
    <svg class="back-pattern" width="680" height="388" viewBox="0 0 680 388">
      <defs>
        <radialGradient id="swirlTone" cx="0.4" cy="0.45" r="0.6">
          <stop offset="0" stop-color="#9fd8c9" stop-opacity="0.45"/>
          <stop offset="1" stop-color="#9fd8c9" stop-opacity="0"/>
        </radialGradient>
      </defs>
      <rect role="img" aria-label="Soft decorative swirl pattern" width="680" height="388" fill="url(#swirlTone)"/>
    </svg>
    <div class="back-info">
      <div class="brand-name">Fern Lattice</div>
      <div class="brand-tagline">Table and Chair Rentals</div>
    </div>
    <div class="back-web">www.fernlatticerentals.com</div>
    <div class="back-rule"></div>
  </section>

</main>
</body>
</html>
```